business card for horse saddlery

after a new business card for our saddlery, i will add 2 logos we have previously used and they can be used (or not) . Any images can be used from our website also at www.harrowfields.net.au, I have also added our brand logo, which may be good to incorporate on back ? we have over 15, 000 items online, ship Australia Wide.

Target Market(s)

horse owners

Industry/Entity Type

Retail - Equestrian

Contact Information for Business Card

Harrowfield Horse Supplies, 1300 48 62 90, www.harrowfields.net.au, 27 Lindqvist Rd Marrowbank Q 4587

Requirements
Must have
• trailgem is our brand so trailgem logo on back as 'distributers of', easy to read
Nice to have
• professional but fun
Should not have
• double sided (description wont save double sided)

```html
<!DOCTYPE html>
<html lang="en">
<head>
<meta charset="utf-8">
<title>Harrowfield Horse Supplies – Business Card</title>
<link rel="stylesheet" href="https://fonts.googleapis.com/css2?family=Cinzel:wght@500;600&family=Poppins:wght@400;500;600;700&display=swap">
<style>
  :root {
    --page: #ffffff;
    --navy: #04163f;
    --navy-deep: #03123a;
    --accent: #4a78f0;
    --ink: #ffffff;
    --serif: "Cinzel", "Times New Roman", serif;
    --sans: "Poppins", Arial, sans-serif;
  }
  * { box-sizing: border-box; margin: 0; padding: 0; }
  html, body {
    width: 718px; height: 1200px; overflow: hidden;
    background: var(--page);
  }
  .canvas {
    position: relative; width: 718px; height: 1200px;
  }
  .card {
    position: absolute; top: 330px;
    width: 309px; height: 541px;
    background: linear-gradient(160deg, var(--navy) 0%, var(--navy-deep) 100%);
    color: var(--ink);
    box-shadow: 0 4px 8px rgba(0, 0, 0, 0.25);
    overflow: hidden;
  }
  .card--front { left: 21px; }
  .card--back { left: 387px; }
  .card > * {
    position: absolute; left: 0; right: 0; text-align: center;
  }

  /* front */
  .brand-mark {
    top: 150px;
    display: flex; align-items: center; justify-content: center; gap: 8px;
    font-family: var(--sans); font-weight: 500; font-size: 21px;
  }
  .brand-mark__dot {
    width: 12px; height: 12px; border-radius: 50%; background: var(--ink);
  }
  .headline {
    top: 303px;
    font-family: var(--sans); font-size: 21.5px; line-height: 1.17;
  }
  .headline__bold { font-weight: 700; display: block; }
  .headline__figure { color: var(--accent); }
  .headline__light { font-weight: 400; display: block; }
  .front-url {
    top: 497px;
    font-family: var(--sans); font-weight: 600; font-size: 15px; letter-spacing: 0.8px;
  }

  /* back */
  .company-name {
    top: 52px;
    font-family: var(--serif); font-weight: 600; font-size: 29px; letter-spacing: 0.3px;
    line-height: 1;
  }
  .company-tagline {
    top: 92px;
    font-family: var(--sans); font-weight: 600; font-size: 17px; letter-spacing: 3.6px;
    color: var(--accent);
  }
  .distributor-label {
    top: 154px;
    font-family: var(--sans); font-weight: 600; font-size: 7.5px; letter-spacing: 1.6px;
    color: var(--accent);
  }
  .distributor-brand {
    top: 248px;
    font-family: var(--serif); font-weight: 600; font-size: 27px; letter-spacing: 0.5px;
  }
  .contact {
    font-family: var(--sans); font-weight: 600; font-size: 14.5px; line-height: 1.3;
  }
  .contact-icon {
    display: flex; justify-content: center;
  }
  .contact-icon svg { width: 17px; height: 17px; }
  .icon-phone { top: 322px; }
  .contact-phone { top: 343px; }
  .icon-pin { top: 372px; }
  .contact-address { top: 392px; }
  .icon-web { top: 436px; }
  .contact-web { top: 458px; font-size: 14px; }
</style>
</head>
<body>
<main class="canvas">

  <section class="card card--front" aria-label="Card front">
    <div class="brand-mark">
      <span class="brand-mark__dot"></span>
      <span>harrowfields.net.au</span>
    </div>
    <p class="headline">
      <span class="headline__bold">We have over</span>
      <span class="headline__bold"><span class="headline__figure">15,000</span> items online,</span>
      <span class="headline__light">ship Australia Wide</span>
    </p>
    <p class="front-url">www.harrowfields.net.au</p>
  </section>

  <section class="card card--back" aria-label="Card back">
    <h1 class="company-name">HARROWFIELD</h1>
    <p class="company-tagline">HORSE SUPPLIES</p>
    <p class="distributor-label">DISTRIBUTERS OF</p>
    <p class="distributor-brand">TRAILGEM</p>

    <div class="contact-icon icon-phone">
      <svg viewBox="0 0 20 20" aria-hidden="true">
        <circle cx="10" cy="10" r="10" fill="#fff"/>
        <path d="M7.2 5.5l1.4 1.6-.8 1.3c.6 1.4 1.6 2.4 3 3l1.3-.8 1.6 1.4-.9 1.5c-3.2-.3-6.1-3.2-6.4-6.4z" fill="none" stroke="#04163f" stroke-width="1" stroke-linejoin="round"/>
      </svg>
    </div>
    <p class="contact contact-phone">1300 48 62 90</p>

    <div class="contact-icon icon-pin">
      <svg viewBox="0 0 20 20" aria-hidden="true">
        <circle cx="10" cy="10" r="10" fill="#fff"/>
        <path d="M10 15s-3.6-3.7-3.6-6.3a3.6 3.6 0 0 1 7.2 0C13.6 11.3 10 15 10 15z" fill="none" stroke="#04163f" stroke-width="1"/>
        <circle cx="10" cy="8.7" r="1.2" fill="none" stroke="#04163f" stroke-width="1"/>
      </svg>
    </div>
    <p class="contact contact-address">27 Lindqvist Rd<br>Marrowbank Q 4587</p>

    <div class="contact-icon icon-web">
      <svg viewBox="0 0 20 20" aria-hidden="true">
        <circle cx="10" cy="10" r="10" fill="#fff"/>
        <g fill="none" stroke="#04163f" stroke-width="0.9">
          <circle cx="10" cy="10" r="4.6"/>
          <ellipse cx="10" cy="10" rx="2" ry="4.6"/>
          <path d="M5.4 10h9.2M6 7.6h8M6 12.4h8"/>
        </g>
      </svg>
    </div>
    <p class="contact contact-web">www.harrowfields.net.au</p>
  </section>

</main>
</body>
</html>
```